QVR business card

Need a business card for a company that provides instructional design and elearning development services. The website is here: http://quorvane.studio/

I'm attaching a current logo, as well as the old business card design. While I like to keep it clean, the old design is too simplistic for my liking. The only idea I want to reuse from the old design is placing industry jargon on the back of the card, just need a better way to present it. But if you have other ideas for the back--feel free to experiment.

Please use the colors complementary to the color we have on the website. Thank you!

```html
<!DOCTYPE html>
<html lang="en">
<head>
<meta charset="utf-8">
<title>QVR business card</title>
<link rel="stylesheet" href="https://fonts.googleapis.com/css2?family=Nunito:wght@700;800&family=Open+Sans:wght@400;600;700&display=swap">
<style>
  :root {
    --teal: #2aa89f;
    --teal-deep: #17948a;
    --teal-light: #3bb7ae;
    --gold: #c9b98a;
    --ink: #454a4a;
    --paper: #ffffff;
    --backdrop: #a8a8a8;
  }
  * { margin: 0; padding: 0; box-sizing: border-box; }
  html, body { width: 1200px; height: 900px; overflow: hidden; }
  body {
    background: var(--backdrop);
    font-family: "Open Sans", Arial, sans-serif;
    position: relative;
  }
  .card {
    position: absolute;
    width: 560px;
    height: 320px;
    overflow: hidden;
  }
  .card-front { left: 80px; top: 90px; background: var(--paper); }
  .card-back {
    left: 560px; top: 490px;
    background: linear-gradient(100deg, var(--teal-light), var(--teal-deep));
  }
  .card-art { position: absolute; inset: 0; }

  .brand {
    position: absolute;
    display: flex;
    align-items: center;
    gap: 14px;
  }
  .brand-mark { width: 34px; height: 34px; background: var(--teal); }
  .brand-name {
    font-family: "Open Sans", Arial, sans-serif;
    font-weight: 700;
    font-size: 50px;
    letter-spacing: 2px;
    color: var(--gold);
    line-height: 1;
  }
  .card-front .brand { left: 34px; top: 50px; }
  .card-back .brand { left: 190px; top: 40px; }
  .card-back .brand-mark { background: var(--paper); }

  .holder-name {
    position: absolute;
    left: 300px; top: 152px;
    font-family: "Nunito", Arial, sans-serif;
    font-weight: 800;
    font-size: 25px;
  }
  .holder-name .first { color: var(--teal); }
  .holder-name .last { color: var(--gold); }

  .contact-list {
    position: absolute;
    left: 32px; top: 196px;
    list-style: none;
    font-size: 14px;
    color: var(--ink);
  }
  .contact-list li { display: flex; align-items: center; gap: 8px; height: 24px; }
  .contact-icon { width: 14px; height: 14px; fill: var(--teal); }

  .help-title {
    position: absolute;
    left: 190px; top: 128px;
    width: 210px;
    font-weight: 600;
    font-size: 20px;
    letter-spacing: 1px;
    color: var(--ink);
    white-space: nowrap;
  }
  .jargon {
    position: absolute;
    font-size: 13px;
    letter-spacing: 1.5px;
    color: var(--ink);
    line-height: 22px;
    word-spacing: 10px;
  }
  .jargon-left { left: 40px; top: 180px; }
  .jargon-right { left: 300px; top: 214px; text-align: right; }
</style>
</head>
<body>

  <section class="card card-front">
    <svg class="card-art" viewBox="0 0 560 320" aria-hidden="true">
      <line x1="0" y1="180" x2="290" y2="180" stroke="var(--teal)" stroke-width="1.5"/>
      <path d="M0,298 Q330,300 560,205 L560,320 L0,320 Z" fill="var(--teal)"/>
      <path d="M0,293 Q330,294 560,196" fill="none" stroke="var(--gold)" stroke-width="6"/>
      <path d="M0,298 Q330,299 560,203" fill="none" stroke="var(--paper)" stroke-width="2"/>
    </svg>
    <div class="brand">
      <span class="brand-mark"></span>
      <span class="brand-name">QVR</span>
    </div>
    <h1 class="holder-name"><span class="first">Marcus</span> <span class="last">Velden</span></h1>
    <ul class="contact-list">
      <li>
        <svg class="contact-icon" viewBox="0 0 16 16"><path d="M3 1l3 3-2 2c1 2 3 4 5 5l2-2 3 3-2 3C7 15 1 9 1 3z"/></svg>
        555-014-2287
      </li>
      <li>
        <svg class="contact-icon" viewBox="0 0 16 16"><path d="M1 3h14v10H1z M1 3l7 6 7-6" stroke="var(--paper)" stroke-width="1"/></svg>
        mvelden@quorvane.studio
      </li>
      <li>
        <svg class="contact-icon" viewBox="0 0 16 16"><circle cx="8" cy="8" r="7"/><path d="M1 8h14M8 1c-3 4-3 10 0 14M8 1c3 4 3 10 0 14" stroke="var(--paper)" stroke-width="1" fill="none"/></svg>
        www.quorvane.studio
      </li>
    </ul>
  </section>

  <section class="card card-back">
    <svg class="card-art" viewBox="0 0 560 320" aria-hidden="true">
      <line x1="40" y1="134" x2="175" y2="134" stroke="var(--ink)" stroke-width="3"/>
      <line x1="415" y1="164" x2="530" y2="164" stroke="var(--ink)" stroke-width="3"/>
    </svg>
    <div class="brand">
      <span class="brand-mark"></span>
      <span class="brand-name">QVR</span>
    </div>
    <h2 class="help-title">HOW CAN WE HELP?</h2>
    <p class="jargon jargon-left">MOBILE LEARNING SCORM<br>INSTRUCTIONAL DESIGN LMS<br>MOOCS ELEARNING HTML5</p>
    <p class="jargon jargon-right">ADULT LEARNING THEORY<br>GAMIFICATION CLASSROOM<br>XAPI BLENDED LEARNING</p>
  </section>

</body>
</html>
```